RW Framewell Inc Business cards

We need business cards using our existing logo but slightly modified. Right now the logo says RW Loadbearing Masonry. We want to keep the RW part of the design, but replace the Structural Concrete portion with "FRAMEWELL". Please see the attached file.
Ideally this would be a blank template so we can add Different Names, titles, and phone numbers later.
On the one side we want only the logo and on the other side the detail. I'm attaching an example for you to see.
Please reach out with any other questions. Our address and other details will be given out once we find a design we like.

Target Market(s)

Construction Industry

```html
<!DOCTYPE html>
<html lang="en">
<head>
<meta charset="utf-8">
<title>RW Framewell Inc – Business Cards</title>
<link rel="stylesheet" href="https://fonts.googleapis.com/css2?family=Archivo+Black&family=Roboto:wght@400;500&display=swap">
<style>
  :root {
    --brand-blue: #1f74c0;
    --brand-blue-deep: #1a66ab;
    --steel-grey: #808285;
    --text-grey: #6d6e71;
    --card-white: #ffffff;
    --stage: #e4e5e7;
    --divider: #c9cacc;
  }
  * { box-sizing: border-box; margin: 0; padding: 0; }
  html, body {
    width: 1200px;
    height: 1015px;
    overflow: hidden;
    background: var(--stage);
  }
  .sheet {
    position: relative;
    width: 1200px;
    height: 1015px;
  }
  .card {
    position: absolute;
    left: 190px;
    width: 820px;
    height: 468px;
    box-shadow: 0 6px 18px rgba(0, 0, 0, 0.18);
    overflow: hidden;
  }

  /* Back side: logo only */
  .card-back {
    top: 25px;
    background: var(--brand-blue);
  }
  .card-back .pattern-field {
    position: absolute;
    inset: 0;
    background: linear-gradient(135deg, var(--brand-blue) 0%, var(--brand-blue-deep) 100%);
  }
  .card-back .back-mark {
    position: absolute;
    left: 560px;
    top: 172px;
    font-family: "Archivo Black", sans-serif;
    font-size: 58px;
    letter-spacing: 2px;
    color: var(--card-white);
  }

  /* Front side: details */
  .card-front {
    top: 522px;
    background: var(--card-white);
  }
  .brand-block {
    position: absolute;
    left: 66px;
    top: 176px;
    display: flex;
    align-items: center;
    gap: 16px;
  }
  .brand-square {
    width: 30px;
    height: 30px;
    flex: none;
    background: var(--steel-grey);
  }
  .brand-name {
    font-family: "Archivo Black", sans-serif;
    font-size: 37px;
    line-height: 1.05;
    color: var(--brand-blue);
    letter-spacing: 1px;
    white-space: nowrap;
  }
  .divider {
    position: absolute;
    left: 446px;
    top: 70px;
    width: 1px;
    height: 290px;
    background: linear-gradient(to bottom, rgba(201,202,204,0), var(--divider) 20%, var(--divider) 80%, rgba(201,202,204,0));
  }
  .details {
    position: absolute;
    left: 486px;
    top: 110px;
  }
  .person-name {
    font-family: "Archivo Black", sans-serif;
    font-size: 26px;
    color: var(--brand-blue);
    letter-spacing: 0.5px;
    line-height: 1.1;
    white-space: nowrap;
  }
  .person-title {
    font-family: "Roboto", sans-serif;
    font-size: 19px;
    color: var(--text-grey);
    margin-top: 2px;
  }
  .contact-list {
    list-style: none;
    margin-top: 26px;
  }
  .contact-list li {
    display: flex;
    align-items: center;
    gap: 10px;
    font-family: "Roboto", sans-serif;
    font-size: 19px;
    color: var(--text-grey);
    line-height: 1.55;
    white-space: nowrap;
  }
  .contact-list svg {
    width: 20px;
    height: 20px;
    flex: none;
  }
  .contact-list .accent { color: var(--brand-blue); }
</style>
</head>
<body>
<main class="sheet">

  <section class="card card-back" aria-label="Business card back">
    <div class="pattern-field" role="img" aria-label="Blue field with a repeating embossed monogram pattern"></div>
    <div class="back-mark">RW</div>
  </section>

  <section class="card card-front" aria-label="Business card front">
    <div class="brand-block">
      <span class="brand-square"></span>
      <div class="brand-name">RW<br>FRAMEWELL</div>
    </div>

    <div class="divider"></div>

    <div class="details">
      <h1 class="person-name">DANIEL HARPER</h1>
      <p class="person-title">Managing Director</p>
      <ul class="contact-list">
        <li>
          <svg viewBox="0 0 20 20" aria-hidden="true"><path fill="#1f74c0" d="M5 2.5c.6-.4 1.4-.3 1.8.3l1.6 2.3c.4.6.3 1.3-.2 1.8l-1 .9c.7 1.6 1.9 2.9 3.6 3.7l.9-1c.5-.5 1.2-.6 1.8-.2l2.3 1.6c.6.4.7 1.2.3 1.8l-1 1.4c-.6.8-1.600 1.100-2.500.800C8.1 14.3 5.1 11.3 3.6 6.8c-.3-.9 0-1.9.8-2.5z"/></svg>
          <span>044-987 654 321</span>
        </li>
        <li>
          <svg viewBox="0 0 20 20" aria-hidden="true"><rect x="2" y="4.5" width="16" height="11" fill="#1f74c0"/><path d="M2.5 5l7.5 6 7.5-6" fill="none" stroke="#fff" stroke-width="1.4"/></svg>
          <span>info@framewell.com</span>
        </li>
        <li>
          <svg viewBox="0 0 20 20" aria-hidden="true"><g fill="none" stroke="#1f74c0" stroke-width="1.5"><circle cx="10" cy="10" r="7.5"/><ellipse cx="10" cy="10" rx="3.3" ry="7.5"/><path d="M2.5 10h15M4 6h12M4 14h12"/></g></svg>
          <span>www.<span class="accent">framewellsite</span>.com</span>
        </li>
      </ul>
    </div>
  </section>

</main>
</body>
</html>
```